Business Card Design

Electronic Security Installation Specialists

Check out our website at www.tallbrookllc.com to see what we do.

Industry/Entity Type

Business

Contact Information for Business Card

Tall Brook
Marjorie Hadley
281 Orchard Rise
Mapleton, WV 25871

Colors
3176b5
0455a3
ffffff

```html
<!DOCTYPE html>
<html lang="en">
<head>
<meta charset="utf-8">
<title>Tall Brook – Business Card</title>
<link href="https://fonts.googleapis.com/css2?family=Exo+2:wght@400;600&family=Michroma&display=swap" rel="stylesheet">
<style>
  :root{
    --brand-blue:#0455a3;
    --brand-blue-light:#3176b5;
    --white:#ffffff;
    --card-shade:#e6e8ea;
    --silver:#b9bec4;
    --silver-dark:#8a9096;
    --ink:#2b2f33;
    --ink-soft:#4a4f55;
    --backdrop:#eceeef;
  }
  html,body{margin:0;padding:0;}
  body{
    width:1200px;height:899px;overflow:hidden;
    background:var(--backdrop);
    position:relative;
    font-family:"Exo 2",sans-serif;
  }
  .business-card{
    position:absolute;left:100px;top:164px;
    width:1000px;height:572px;
    border-radius:42px;overflow:hidden;
    background:linear-gradient(160deg,var(--white) 0%,#f6f7f8 45%,var(--card-shade) 100%);
    box-shadow:0 10px 30px rgba(0,0,0,.12);
  }
  .corner-accents{position:absolute;inset:0;width:100%;height:100%;}
  .brand-mark{
    position:absolute;left:380px;top:58px;
    display:flex;align-items:center;gap:14px;
  }
  .brand-mark__dot{
    width:26px;height:26px;border-radius:50%;
    background:var(--brand-blue);
  }
  .brand-mark__name{
    font-family:"Exo 2",sans-serif;font-weight:600;
    font-size:40px;color:var(--brand-blue);letter-spacing:1px;
  }
  .contact-list{
    position:absolute;left:62px;top:318px;
    list-style:none;margin:0;padding:0;
  }
  .contact-list li{
    display:flex;align-items:center;gap:14px;
    height:29px;font-size:17px;color:var(--ink-soft);letter-spacing:.5px;
  }
  .contact-list svg{width:17px;height:17px;fill:var(--ink-soft);flex:none;}
  .person{position:absolute;left:555px;top:338px;}
  .person__name{
    font-family:"Michroma",sans-serif;font-size:24px;font-weight:400;
    color:var(--ink);letter-spacing:2px;margin:0;
    text-transform:uppercase;white-space:nowrap;
  }
  .person__role{
    font-size:18px;color:var(--ink-soft);
    margin:6px 0 0 60px;letter-spacing:.5px;
  }
  .address{
    position:absolute;left:610px;top:440px;
    font-size:18px;line-height:26px;color:var(--ink-soft);
    font-style:normal;letter-spacing:.5px;
  }
</style>
</head>
<body>
  <article class="business-card">
    <svg class="corner-accents" viewBox="0 0 1000 572" preserveAspectRatio="none" aria-hidden="true">
      <defs>
        <linearGradient id="blueBand" x1="0" y1="0" x2="1" y2="1">
          <stop offset="0" stop-color="#0455a3"/>
          <stop offset="1" stop-color="#3176b5"/>
        </linearGradient>
        <linearGradient id="silverBand" x1="0" y1="0" x2="1" y2="0">
          <stop offset="0" stop-color="#8a9096"/>
          <stop offset=".5" stop-color="#b9bec4"/>
          <stop offset="1" stop-color="#ffffff"/>
        </linearGradient>
      </defs>
      <path d="M0 0 H250 C170 20 110 70 70 150 C40 210 20 250 0 270 Z" fill="url(#silverBand)"/>
      <path d="M0 0 H225 C150 22 95 70 60 140 C35 190 18 225 0 245 Z" fill="url(#blueBand)"/>
      <path d="M1000 572 H730 C820 555 890 505 930 430 C955 385 975 345 1000 320 Z" fill="url(#silverBand)"/>
      <path d="M1000 572 H760 C845 552 905 505 942 440 C965 400 982 368 1000 345 Z" fill="url(#blueBand)"/>
    </svg>

    <div class="brand-mark">
      <span class="brand-mark__dot"></span>
      <span class="brand-mark__name">Tall Brook</span>
    </div>

    <ul class="contact-list">
      <li><svg viewBox="0 0 24 24"><path d="M6.6 10.8a15 15 0 0 0 6.6 6.6l2.2-2.2a1 1 0 0 1 1-.25 11.4 11.4 0 0 0 3.6.57 1 1 0 0 1 1 1V20a1 1 0 0 1-1 1A17 17 0 0 1 3 4a1 1 0 0 1 1-1h3.5a1 1 0 0 1 1 1c0 1.25.2 2.45.57 3.57a1 1 0 0 1-.25 1z"/></svg>304 555 0142</li>
      <li><svg viewBox="0 0 24 24"><rect x="7" y="2" width="10" height="20" rx="2"/></svg>304 555 0178</li>
      <li><svg viewBox="0 0 24 24"><path d="M6 2h10v6H6zM3 9h18v9h-3v4H6v-4H3z"/></svg>304 555 0193</li>
      <li><svg viewBox="0 0 24 24"><path d="M2 5h20v14H2z M2 5l10 8 10-8"/></svg>info@tallbrookllc.com</li>
      <li><svg viewBox="0 0 24 24"><circle cx="12" cy="12" r="10"/></svg>www.tallbrookllc.com</li>
    </ul>

    <div class="person">
      <h1 class="person__name">Marjorie Hadley</h1>
      <p class="person__role">Managing Director</p>
    </div>

    <address class="address">281 Orchard Rise<br>Mapleton, WV 25871</address>
  </article>
</body>
</html>
```